Lantern Petals Website v.1 - attract floral shop franchisees

I need a simple information website for my new business. We are a franchisor of flower shops. The overall purpose of the website is to promote the company and the service, especially to potential franchisees and retailers. Only about 4 pages are required including homepage, About, For Supermarkets, For Franchisees, and Contact. No special functions are required except the site will have two separate inquiry forms that must be filled out online and submitted via automated email. Similarly, an email form should be linked from the Contact page. I have a logo and business cards designed by ArtMingle, and I would like the site to have a consistent color scheme and style. The key to design will be to express the joy and love associated with flowers and floral bouquets.
IMPORTANT - I will be exporting the website design to Wordpress CMS in a site hosted by HostNimbus. For smooth integration into WordPress hosted by HostNimbus, the designer should build the site using a WordPress-friendly format. Ideally, they should use HTML, CSS, and PHP. Creating a custom theme or using a page builder that exports to WordPress-compatible files is best. This ensures the site can be easily imported and managed within WordPress.

Target Market(s)

Potential franchisees (existing florists or creative types who might like to own a floral business) and supermarkets who might want us to run their floral department

Industry/Entity Type

Floral retailing

Requirements
Must have
• A brand theme that is beautiful, consistent throughout and builds on the logo design
Nice to have
• Show gender and ethnic diversity in customers and florists. Pictures of happy florists (for franchisees) and pictures of amazing floral department displays (for supermarkets)

```html
<!DOCTYPE html>
<html lang="en">
<head>
<meta charset="utf-8">
<title>Lantern Petals – Flower Shops</title>
<link rel="stylesheet" href="https://fonts.googleapis.com/css2?family=Allura&family=Open+Sans:wght@300;400;600;700&display=swap">
<style>
:root{
  --green:#17934a;
  --orange:#f29a1f;
  --text:#4f4f4f;
  --dark:#222;
  --cream:#fdf6ee;
  --mist:#ececec;
  --white:#ffffff;
}
html,body{margin:0;padding:0;overflow:hidden;}
body{background:var(--white);}
.page{position:relative;width:1200px;height:2780px;overflow:hidden;font-family:"Open Sans",sans-serif;color:var(--text);background:var(--white);}
.abs{position:absolute;}

/* hero */
.hero{left:0;top:0;width:1200px;height:720px;background:linear-gradient(120deg,#f3eeee 0%,#eeeeee 45%,#e6e6e6 100%);}
.hero-photo{left:540px;top:86px;width:660px;height:610px;border-radius:46% 40% 30% 50%;background:radial-gradient(circle at 48% 42%,#faf3ef 0%,#e8c6cf 30%,#c88a9c 48%,#6f8c55 68%,rgba(90,110,70,0) 80%);}
.brand{left:140px;top:70px;display:flex;align-items:center;gap:14px;}
.brand-dot{width:40px;height:40px;border-radius:50%;background:var(--orange);}
.brand-name{font-family:"Open Sans",sans-serif;font-weight:600;font-size:34px;color:var(--orange);white-space:nowrap;}
.nav{top:37px;left:480px;width:620px;height:32px;}
.nav a{position:absolute;top:0;height:32px;line-height:32px;font-size:14px;color:var(--dark);text-decoration:none;letter-spacing:.2px;white-space:nowrap;}
.nav a.active{background:var(--green);color:var(--white);border-radius:16px;padding:0 13px;}
.script{font-family:"Allura",cursive;color:var(--orange);font-weight:400;margin:0;line-height:1;white-space:nowrap;}
.hero-title{left:132px;top:228px;font-size:112px;}
.hero-sub{left:140px;top:338px;font-size:20px;font-weight:300;color:#333;margin:0;}
.btn{display:flex;align-items:center;background:var(--green);color:var(--white);font-weight:700;font-size:14px;text-decoration:none;border-radius:24px;padding-left:28px;box-sizing:border-box;height:47px;white-space:nowrap;}
.btn::after{content:"";position:absolute;right:12px;top:-8px;width:18px;height:18px;border-radius:50%;background:var(--orange);border:3px solid var(--white);}
.btn-a{left:139px;top:408px;width:320px;}
.btn-b{left:139px;top:474px;width:381px;}

/* welcome */
.mark{left:200px;top:800px;width:280px;height:280px;border:10px solid var(--orange);border-radius:50%;display:flex;align-items:center;justify-content:center;box-sizing:border-box;}
.mark span{font-weight:600;font-size:30px;color:var(--green);white-space:nowrap;}
.welcome-kicker{left:580px;top:752px;font-size:24px;color:var(--dark);margin:0;}
.welcome-title{left:578px;top:790px;font-size:76px;}
.dashes{height:3px;width:62px;}
.dashes::before,.dashes::after{content:"";position:absolute;top:0;height:3px;background:var(--green);}
.dashes::before{left:0;width:40px;}
.dashes::after{left:50px;width:12px;}
.copy{margin:0;font-size:19px;font-weight:300;line-height:28.7px;color:var(--text);}
.welcome-copy{left:582px;top:925px;width:440px;}
.btn-more{width:157px;}

/* supermarkets */
.markets{left:0;top:1286px;width:1200px;height:580px;background:var(--cream);}
.markets-photo{left:669px;top:1286px;width:531px;height:560px;background:linear-gradient(90deg,rgba(253,246,238,1) 0%,rgba(244,196,170,.6) 18%,#f4c3b0 35%,#f9d98a 55%,#e0899f 78%,#c95f86 100%);}
.markets-title{left:132px;top:1340px;font-size:76px;}
.markets-copy{left:139px;top:1494px;width:500px;font-size:19.5px;line-height:27.2px;}

/* franchisees */
.franchise{left:0;top:1900px;width:1200px;height:626px;background:var(--mist);}
.franchise-photo{left:97px;top:1937px;width:507px;height:545px;border-radius:42% 46% 10% 10%;background:radial-gradient(circle at 50% 40%,#f2e0e2 0%,#d98a95 30%,#a46bb0 55%,#c7414a 70%,rgba(236,236,236,0) 88%);}
.franchise-title{left:650px;top:1972px;font-size:76px;}
.franchise-copy{left:658px;top:2124px;width:420px;}

/* footer */
.footer{left:0;top:2540px;width:1200px;height:240px;background:var(--green);}
.footer-brand{left:140px;top:2620px;display:flex;align-items:center;gap:16px;}
.footer-brand .brand-dot{width:56px;height:56px;background:var(--white);}
.footer-brand .brand-name{color:var(--white);font-size:46px;}
.follow{left:849px;top:2607px;font-size:13px;color:var(--white);margin:0;white-space:nowrap;}
.social{left:944px;top:2604px;display:flex;gap:14px;}
.social span{width:20px;height:20px;border:2px solid var(--white);border-radius:50%;box-sizing:border-box;}
.footer-nav a{position:absolute;top:2664px;font-size:13px;color:var(--white);text-decoration:none;white-space:nowrap;}
.copyright{left:772px;top:2712px;width:300px;text-align:right;font-size:13px;color:var(--white);margin:0;white-space:nowrap;}
</style>
</head>
<body>
<div class="page">

  <section class="abs hero"></section>
  <div class="abs hero-photo" role="img" aria-label="Hand holding a colourful birthday bouquet of peonies, dahlias and roses"></div>

  <div class="abs brand"><span class="brand-dot"></span><span class="brand-name">Lantern Petals</span></div>

  <nav class="abs nav">
    <a class="active" href="#" style="left:0">HOME</a>
    <a href="#" style="left:90px">ABOUT US</a>
    <a href="#" style="left:194px">FOR SUPERMARKETS</a>
    <a href="#" style="left:372px">FOR FRANCHISEES</a>
    <a href="#" style="left:522px">CONTACT</a>
  </nav>

  <h1 class="abs script hero-title">Flower Shops</h1>
  <p class="abs hero-sub">Fresh flowers convey beauty and love</p>
  <a class="abs btn btn-a" href="#">NEW FLORIST FRANCHISE INQUIRY</a>
  <a class="abs btn btn-b" href="#">PROFESSIONAL FLORIST FRANCHISE INQUIRY</a>

  <svg class="abs" style="left:0;top:580px" width="1200" height="142" viewBox="0 580 1200 142" aria-hidden="true">
    <path d="M0,690 C250,640 500,670 700,700 C900,720 1100,670 1200,645 L1200,722 L0,722Z" fill="var(--white)"/>
    <path d="M0,628 C150,592 300,582 450,620 C600,668 750,698 900,682 C1050,666 1150,646 1200,636 L1200,650 C1100,672 950,702 800,706 C650,706 500,662 350,642 C200,626 80,650 0,664Z" fill="var(--orange)"/>
    <path d="M0,718 C100,662 250,636 520,654 C300,650 120,682 0,702Z" fill="var(--green)"/>
  </svg>

  <div class="abs mark" role="img" aria-label="Lantern Petals brand mark"><span>Lantern Petals</span></div>
  <p class="abs welcome-kicker">Welcome to</p>
  <h2 class="abs script welcome-title">Lantern Petals</h2>
  <div class="abs dashes" style="left:582px;top:881px"></div>
  <p class="abs copy welcome-copy">Fresh flowers convey beauty and love, and in our view should become something every person regularly enjoys.&nbsp; Lantern Petals is an entrepreneurial company created to make top quality fresh flowers and professionally - designed bouquets accessible to every consumer at affordable prices.</p>
  <a class="abs btn btn-more" href="#" style="left:586px;top:1160px">READ MORE</a>

  <section class="abs markets"></section>
  <div class="abs markets-photo" role="img" aria-label="Close-up of yellow gerberas and pink roses in a floral display"></div>
  <h2 class="abs script markets-title">For Supermarkets</h2>
  <div class="abs dashes" style="left:139px;top:1445px"></div>
  <p class="abs copy markets-copy">Lantern Petals works with some of the country’s largest and most progressive supermarkets to provide franchisee ownership and operation of their strategically important floral departments.&nbsp; Supermarkets find that Lantern Petals is able to improve their financial outcomes, provide attentive customer service and satisfaction, and lift the quality of the entire store environment.</p>
  <a class="abs btn btn-more" href="#" style="left:142px;top:1752px">READ MORE</a>

  <svg class="abs" style="left:0;top:1820px" width="1200" height="120" viewBox="0 1820 1200 120" aria-hidden="true">
    <rect x="0" y="1820" width="1200" height="120" fill="var(--mist)"/>
    <path d="M0,1820 L1200,1820 L1200,1825 C1000,1815 800,1830 600,1862 C400,1892 200,1874 0,1848Z" fill="var(--cream)"/>
    <path d="M0,1848 C200,1874 400,1892 600,1862 C800,1830 1000,1815 1200,1825 L1200,1845 C1000,1835 820,1845 620,1880 C420,1912 200,1894 0,1864Z" fill="var(--orange)"/>
    <path d="M690,1872 C860,1842 1050,1850 1200,1888 L1200,1932 C1080,1888 900,1866 690,1872Z" fill="var(--green)"/>
  </svg>

  <section class="abs franchise"></section>
  <div class="abs franchise-photo" role="img" aria-label="Hands holding up a large mixed bouquet of roses, stock and daisies"></div>
  <h2 class="abs script franchise-title">For Franchisees</h2>
  <div class="abs dashes" style="left:658px;top:2076px"></div>
  <p class="abs copy franchise-copy">Lantern Petals brings the best of professional florists and supermarkets together for the benefit of consumers.&nbsp; It supports a national network of owner-operator franchisees, who in many cases are multi-site professional florists, with comprehensive services to enhance franchise profitability.</p>
  <a class="abs btn btn-more" href="#" style="left:660px;top:2367px">READ MORE</a>

  <footer class="abs footer"></footer>
  <svg class="abs" style="left:0;top:2440px" width="1200" height="122" viewBox="0 2440 1200 122" aria-hidden="true">
    <rect x="0" y="2440" width="1200" height="122" fill="var(--green)"/>
    <path d="M0,2440 L1200,2440 L1200,2492 C1000,2520 800,2530 600,2510 C400,2485 200,2470 0,2490Z" fill="var(--mist)"/>
    <path d="M0,2490 C200,2470 400,2485 600,2510 C800,2530 1000,2520 1200,2492 L1200,2500 C1000,2535 800,2548 600,2532 C400,2515 200,2500 0,2512Z" fill="var(--orange)"/>
    <path d="M0,2512 C200,2500 400,2515 600,2532 C800,2548 1000,2535 1200,2500 L1200,2508 C1000,2548 800,2560 600,2546 C400,2530 200,2520 0,2555Z" fill="var(--white)"/>
  </svg>

  <div class="abs footer-brand"><span class="brand-dot"></span><span class="brand-name">Lantern Petals</span></div>
  <p class="abs follow">FOLLOW US</p>
  <div class="abs social" aria-label="Social links"><span></span><span></span><span></span><span></span></div>
  <nav class="footer-nav">
    <a href="#" style="left:556px">HOME</a>
    <a href="#" style="left:624px">ABOUT US</a>
    <a href="#" style="left:718px">FOR SUPERMARKETS</a>
    <a href="#" style="left:875px">FOR FRANCHISEES</a>
    <a href="#" style="left:1009px">CONTACT</a>
  </nav>
  <p class="abs copyright">COPYRIGHT © 2024 ALL RIGHTS RESERVED</p>

</div>
</body>
</html>
```